Counseling Practice Business Card

I need a professional looking business card incorporating my new logo that was just completed. Card needs to incorporate my name and title, description of my specialty, my address, my phone number, my fax number, my email and my website URL. I need to be able to choose design on/with different paper colors and textures.
I do not have a lot of business card ideas so I am open to anything but I want bold,sharp, clear card without additional designs other than my logo (see attached file info). I am open to different color backgrounds or paper colors including black. I do not like traditional brackets around area codes in phone number or dashes between numbers in phone number. Am open to other ways of presenting including periods between numbers as appropriate. I do not know enough to know what I like yet but I want card to coordinate and work together with my logo. My practice emphasizes natural mental health interventions so any use of color (with background paper color or the blue and green in my logo) that elicits nature is nice. In addition to black, any natural brown or wood looking background might be desirable also. Most of the offerings so far look very similar and boring.

Target Market(s)

Potential therapy clients and other professionals

Contact Information for Business Card

Card information:
Gerald M. Whitcombe, Ph.D.
Licensed Clinical Psychologist
Integrative Health Coach
4812 Marlowe Ridge Blvd SE
Suite 310
Duluth, GA 30096
(770) 415-2983 phone
(770) 581-4096 fax
drgeraldwhitcombe@quillmarsh.net
brightfernwellness.net

Font styles to use
Serif
Sans Serif
Other font styles liked:
• anything that you think looks crisp, clear and easily readable

Requirements
Must have
• Any color used should coordinate with my logo design (see attached files).
• Card should be printed horizontally so top and bottom are longest sides of rectangle.
• Background color or paper color should complement and highlight logo. Do not like a white background. black, grey, brown or any color my logo would blend well with.
Nice to have
• I would like designer to utilize color to highlight letters/name or phone-fax-web symbols.
• Bottom edge of card could be highlighted if appropriate to an idea.
Should not have
• I would NOT want the card to have a pure white background at all.
• No clear cards.
• Cards should be oriented with long sides on bottom and top, NOT sides. DO NOT LIKE THIS THIN TALL ORIENTATION.

```html
<!DOCTYPE html>
<html lang="en">
<head>
<meta charset="utf-8">
<title>Brightfern Counseling – Business Card</title>
<link href="https://fonts.googleapis.com/css2?family=Roboto:wght@400;500&family=Roboto+Condensed:wght@600&display=swap" rel="stylesheet">
<style>
  :root {
    --page-bg: #e4e1dc;
    --card-bg: #f3f2ef;
    --card-edge: #d4d2cd;
    --brand-blue: #2d6aa3;
    --brand-green: #1e6b3b;
    --accent-teal: #1f7070;
    --text-dark: #3a3a3a;
    --text-mid: #4a4a4a;
    --icon: #3f4d55;
  }
  * { margin: 0; padding: 0; box-sizing: border-box; }
  html, body { width: 1200px; height: 1054px; overflow: hidden; }
  body { background: var(--page-bg); position: relative; font-family: "Roboto", Arial, sans-serif; }

  .business-card {
    position: absolute; left: 80px; top: 213px; width: 1040px; height: 627px;
    background: var(--card-bg); border: 1px solid var(--card-edge); border-radius: 4px;
    box-shadow: 0 10px 30px rgba(0,0,0,0.12);
    overflow: hidden;
  }

  .brand-name {
    position: absolute; right: 58px; top: 120px;
    font-family: "Roboto", Arial, sans-serif; font-weight: 500;
    font-size: 50px; color: var(--brand-blue); letter-spacing: 0.5px;
  }

  .edge-tab {
    position: absolute; left: -12px; top: 290px; width: 36px; height: 119px;
    background: var(--accent-teal); border-radius: 0 60px 60px 0;
  }

  .holder-name {
    position: absolute; left: 51px; top: 304px;
    font-family: "Roboto Condensed", Arial, sans-serif; font-weight: 600;
    font-size: 39px; color: var(--brand-blue);
  }
  .holder-title {
    position: absolute; left: 51px; top: 362px;
    font-size: 22px; color: var(--text-mid);
  }
  .title-rule {
    position: absolute; left: 263px; top: 379px; width: 724px; height: 3px;
    background: linear-gradient(90deg, var(--brand-blue), var(--brand-green));
  }

  .contact-list { position: absolute; left: 63px; top: 443px; list-style: none; }
  .contact-list li {
    display: flex; align-items: center; height: 33px;
    font-size: 24px; color: var(--text-dark);
  }
  .contact-list svg { width: 20px; height: 20px; margin-right: 17px; fill: var(--icon); flex: none; }

  .address {
    position: absolute; right: 58px; top: 509px; text-align: right;
    font-size: 24px; line-height: 33px; color: var(--text-dark);
  }
</style>
</head>
<body>
  <div class="business-card">
    <div class="brand-name">Brightfern Counseling</div>

    <div class="edge-tab"></div>
    <div class="holder-name">John Doe Smith</div>
    <div class="holder-title">Managing Director</div>
    <div class="title-rule"></div>

    <ul class="contact-list">
      <li>
        <svg viewBox="0 0 20 20" aria-hidden="true"><path d="M2 6c0-2 3-3 8-3s8 1 8 3v2h-4V6.5c-1-.4-2.5-.6-4-.6s-3 .2-4 .6V8H2z"/><path d="M5 9h10l2 8H3z"/><circle cx="10" cy="13" r="2" fill="#f3f2ef"/></svg>
        812.555.0140
      </li>
      <li>
        <svg viewBox="0 0 20 20" aria-hidden="true"><rect x="5" y="2" width="10" height="5"/><path d="M2 8h16v7h-3v-3H5v3H2z"/><rect x="6" y="13" width="8" height="5"/></svg>
        812.555.0141
      </li>
      <li>
        <svg viewBox="0 0 20 20" aria-hidden="true"><path d="M1 4h18v12H1z"/><path d="M1 4l9 7 9-7" fill="none" stroke="#f3f2ef" stroke-width="1.6"/></svg>
        www.yourwebsite.com
      </li>
      <li>
        <svg viewBox="0 0 20 20" aria-hidden="true"><circle cx="10" cy="10" r="8.5"/><path d="M1.5 10h17M10 1.5v17M10 1.5c-3 3-3 14 0 17M10 1.5c3 3 3 14 0 17" fill="none" stroke="#f3f2ef" stroke-width="1.2"/></svg>
        yourname@yourwebsite.com
      </li>
    </ul>

    <div class="address">
      234 Anywhere St., Any City,<br>
      Any Town, US 123456
    </div>
  </div>
</body>
</html>
```